Online homewares store needs a web design

We need a web design for a new high-end online homewares store. We are starting small with only 5 major categories.

Rugs
Bathe
Dine
Decorative
Sleep

This is just for design. No coding needed.

Please make high-end, sophisticated and minimal.

I have included some pictures to give you an idea of the products. I would like to showcase some of the pictures on the web page.

The website will be using an e-commerce function.

I have included the logo studio nine harbors.

I like this website
http://mapleandquarrylane.example/

or

borvanest.example.au

Simple but effective - not too busy

Project Deadline Extended
Reason: I would like to extend my deadline to give designers more time to do quality work - as requested!! Thanks.

Target Market(s)

Females in the age bracket of 25-45

Males who are very house proud 25-45

Industry/Entity Type

Store

Requirements
Must have
• Upmarket

```html
<!DOCTYPE html>
<html lang="en">
<head>
<meta charset="utf-8">
<title>studio nine harbors</title>
<link href="https://fonts.googleapis.com/css2?family=Quicksand:wght@400&family=Lato:wght@400;700&family=Oswald:wght@400&family=Lobster+Two:ital@1&display=swap" rel="stylesheet">
<style>
:root{
  --ink:#000;
  --pink:#e3306e;
  --dark:#1d1d1d;
  --panel:#3a3a3a;
  --yellow:#f4e11c;
  --grey:#e6e6e6;
  --line:#d8d8d8;
  --text:#222;
  --white:#fff;
}
*{margin:0;padding:0;box-sizing:border-box}
html,body{width:825px;height:1200px;overflow:hidden;background:var(--white)}
body{position:relative;font-family:"Lato",sans-serif;color:var(--text)}
.abs{position:absolute}

.topbar{left:0;top:0;width:825px;height:62px;background:var(--ink)}
.brand{left:0;top:12px;width:825px;text-align:center;font-family:"Quicksand",sans-serif;font-size:29px;color:var(--white);letter-spacing:.3px}
.login{left:634px;top:18px;width:47px;height:22px;background:var(--pink);color:var(--white);font-size:10px;text-align:center;line-height:22px}
.cart{left:688px;top:18px;width:46px;height:22px;border:1px solid #444;color:var(--white);font-size:10px;line-height:20px;padding-left:8px}
.cart svg{vertical-align:middle;margin-right:6px}

.navstrip{left:0;top:62px;width:825px;height:33px;background:linear-gradient(#fff,#e4e4e4);border-bottom:1px solid #ddd}
.nav{left:0;top:62px}
.nav a{position:absolute;top:11px;font-size:9px;color:var(--white);text-decoration:none;letter-spacing:.3px;transform:translateX(-50%)}
.nav .sep{position:absolute;top:7px;width:1px;height:19px;background:#333}

.hero{left:90px;top:108px;width:451px;height:219px;background:linear-gradient(160deg,#d9d6cf,#a9a59c 55%,#8a867e)}
.hero-tag{left:119px;top:270px;width:198px;height:31px;background:var(--pink);color:var(--white);font-family:"Lobster Two",cursive;font-style:italic;font-size:17px;text-align:center;line-height:31px}
.cat-panel{left:554px;top:108px;width:180px;height:219px;background:linear-gradient(135deg,#333,#4a4a4a 60%,#5a4f55)}
.cat-title{left:570px;top:124px;font-family:"Lobster Two",cursive;font-style:italic;font-size:21px;color:var(--yellow)}
.cat-list{left:568px;top:168px;list-style:none}
.cat-list li{font-family:"Oswald",sans-serif;font-size:14px;color:var(--white);height:31px}
.cat-list li span{font-family:"Lato",sans-serif;font-size:11px;margin-right:6px}

.promo{width:193px;height:138px;top:350px}
.promo .img{position:absolute;left:0;top:0;width:193px;height:110px}
.promo .off{position:absolute;left:0;top:0;width:64px;height:56px;background:rgba(30,30,30,.85);border-bottom-right-radius:56px}
.promo .off b{position:absolute;left:8px;top:5px;font-family:"Oswald",sans-serif;font-weight:400;font-size:18px;color:var(--yellow);line-height:1}
.promo .off i{position:absolute;left:8px;top:27px;font-style:normal;font-size:11px;color:var(--yellow);letter-spacing:.5px}
.promo .bar{position:absolute;left:0;top:110px;width:193px;height:28px;background:var(--pink);color:var(--white);font-size:13px;line-height:28px;padding-left:11px}
.promo .go{position:absolute;right:0;top:110px;width:44px;height:28px;background:var(--dark);clip-path:polygon(10px 0,100% 0,100% 100%,0 100%)}
.promo .go svg{position:absolute;left:18px;top:9px}
.chev{top:410px}

.section-head{left:90px;top:512px;width:645px;height:24px}
.section-head .rule{position:absolute;left:0;top:19px;width:645px;height:5px;background:var(--grey)}
.section-head .tab{position:absolute;left:0;top:0;width:139px;height:24px;background:var(--panel);clip-path:polygon(0 0,133px 0,139px 24px,0 24px);color:var(--white);font-size:12px;line-height:24px;padding-left:12px}

.card{width:151px;height:182px;border:1px solid var(--line);background:var(--white)}
.card .img{position:absolute;left:3px;top:3px;width:143px;height:104px}
.card .name{position:absolute;left:7px;top:120px;font-size:10px;font-weight:700}
.card .price{position:absolute;right:8px;top:118px;font-size:12px;color:#333}
.card .actions{position:absolute;left:27px;top:148px;width:96px;height:21px;border:1px solid #bbb;border-radius:11px;display:flex}
.card .actions span{flex:1;display:flex;align-items:center;justify-content:center;border-left:1px solid #ccc}
.card .actions span:first-child{border-left:none}

.divider{left:97px;top:946px;width:644px;height:6px;background:repeating-linear-gradient(45deg,#ddd 0 2px,#ececec 2px 4px)}
.partners{left:90px;top:982px;width:645px;display:flex;justify-content:space-between;font-size:12.5px;color:#222}
.partners span{display:flex;align-items:center;gap:4px}
.partners i{display:inline-block;width:10px;height:10px;background:#222;border-radius:50%}

.footer{left:0;top:1022px;width:825px;height:152px;background:repeating-linear-gradient(135deg,#1c1c1c 0 2px,#222 2px 4px)}
.fcol{top:1033px}
.fcol h3{font-weight:400;font-size:13px;color:var(--white);padding-bottom:8px;border-bottom:1px solid #3c3c3c}
.fcol ul{list-style:none;margin-top:6px}
.fcol li{font-size:9px;color:#ddd;height:20.3px}
.fcol li::before{content:"›";margin-right:7px;font-size:11px}
.news p{font-size:9px;color:#ddd;margin-top:8px;line-height:1.35;width:135px}
.news .field{margin-top:8px;width:133px;height:19px;background:var(--white);font-size:7px;color:#888;padding:5px 6px}
.news .btn{margin-top:8px;width:65px;height:19px;background:#b9b9b9;color:#222;font-size:9px;font-weight:700;text-align:center;line-height:19px}
.social li::before{content:none}
.social li{display:flex;align-items:center;gap:11px;height:22.3px}
.social li i{width:16px;height:16px;border-radius:50%;background:#8a8a8a}

.bottom{left:0;top:1174px;width:825px;height:26px;background:var(--pink)}
.copy{left:92px;top:1182px;font-size:9px;color:var(--white)}
.cards{left:590px;top:1179px;display:flex;gap:3px}
.cards i{width:26px;height:17px;background:var(--white);border-radius:2px}
</style>
</head>
<body>

<header>
  <div class="abs topbar"></div>
  <div class="abs brand">studio nine harbors</div>
  <div class="abs login">LOGIN</div>
  <div class="abs cart"><svg width="14" height="11" viewBox="0 0 14 11"><path d="M0 1h3l2 6h7l2-5H4" fill="none" stroke="#fff" stroke-width="1.2"/><circle cx="6" cy="9.5" r="1" fill="#fff"/><circle cx="11" cy="9.5" r="1" fill="#fff"/></svg>0</div>
  <div class="abs navstrip"></div>
  <svg class="abs" style="left:0;top:62px" width="825" height="33"><polygon points="90,0 735,0 716,33 108,33" fill="#000"/></svg>
  <nav class="abs nav">
    <a style="left:198px" href="#">HOME</a><span class="sep" style="left:246px"></span>
    <a style="left:306px" href="#">PRODUCTS</a><span class="sep" style="left:367px"></span>
    <a style="left:416px" href="#">ABOUT</a><span class="sep" style="left:465px"></span>
    <a style="left:514px" href="#">BLOG</a><span class="sep" style="left:563px"></span>
    <a style="left:618px" href="#">CONTACT</a>
  </nav>
</header>

<section>
  <div class="abs hero" role="img" aria-label="Bright window seat room with a woven white rug"></div>
  <div class="abs hero-tag">A Huge Selection Of Rugs</div>
  <div class="abs cat-panel" role="img" aria-label="Colourful felt ball pouf in a soft-focus room"></div>
  <div class="abs cat-title">Shop By Category</div>
  <ul class="abs cat-list">
    <li><span>→</span>Rugs</li><li><span>→</span>Bathe</li><li><span>→</span>Dine</li><li><span>→</span>Decorative</li><li><span>→</span>Sleep</li>
  </ul>
</section>

<section>
  <svg class="abs chev" style="left:90px" width="10" height="20"><path d="M8 1 2 10l6 9" fill="none" stroke="#bbb" stroke-width="1.3"/></svg>
  <svg class="abs chev" style="left:726px" width="10" height="20"><path d="M2 1l6 9-6 9" fill="none" stroke="#bbb" stroke-width="1.3"/></svg>

  <div class="abs promo" style="left:110px">
    <div class="img" role="img" aria-label="Living room with a sofa and red runner rug" style="background:linear-gradient(135deg,#c9a877,#8a5a33 60%,#6e2a1f)"></div>
    <div class="off"><b>20%</b><i>OFF</i></div>
    <div class="bar">Rugs</div>
    <div class="go"><svg width="14" height="10"><path d="M0 3.5h8V0l6 5-6 5V6.5H0z" fill="#fff"/></svg></div>
  </div>
  <div class="abs promo" style="left:316px">
    <div class="img" role="img" aria-label="Stack of rolled white towels" style="background:linear-gradient(135deg,#5a3a1f,#b9a58c 50%,#4a8f86)"></div>
    <div class="off"><b>30%</b><i>OFF</i></div>
    <div class="bar">Bathe</div>
    <div class="go"><svg width="14" height="10"><path d="M0 3.5h8V0l6 5-6 5V6.5H0z" fill="#fff"/></svg></div>
  </div>
  <div class="abs promo" style="left:522px">
    <div class="img" role="img" aria-label="White bowl of grapes on a woven placemat" style="background:linear-gradient(135deg,#e9e3da,#c8a678 55%,#a27d4e)"></div>
    <div class="off"><b>25%</b><i>OFF</i></div>
    <div class="bar">Dine</div>
    <div class="go"><svg width="14" height="10"><path d="M0 3.5h8V0l6 5-6 5V6.5H0z" fill="#fff"/></svg></div>
  </div>
</section>

<section>
  <div class="abs section-head"><div class="rule"></div><div class="tab">LATEST PRODUCTS</div></div>

  <div class="abs card" style="left:90px;top:549px"><div class="img" role="img" aria-label="White sheepskin rug in a lounge" style="background:linear-gradient(160deg,#d8d2c8,#6b4a35 70%)"></div><div class="name">Lorem ipsum</div><div class="price">$199.00</div><div class="actions"><span><svg width="12" height="10"><path d="M0 1h2.5l2 5.5h6L12 2H3.5" fill="none" stroke="#555"/></svg></span><span><svg width="10" height="9"><rect x=".5" y="2.5" width="7" height="6" fill="none" stroke="#555"/><path d="M2.5 .5h7v6" fill="none" stroke="#555"/></svg></span><span><svg width="10" height="10"><circle cx="4" cy="4" r="3.2" fill="none" stroke="#555"/><path d="M6.5 6.5 9.5 9.5" stroke="#555"/></svg></span></div></div>
  <div class="abs card" style="left:255px;top:549px"><div class="img" role="img" aria-label="Pink bedroom with a made bed" style="background:linear-gradient(160deg,#f1dfe2,#d99aae 60%,#c8bcb8)"></div><div class="name">Lorem ipsum</div><div class="price">$100.95</div><div class="actions"><span><svg width="12" height="10"><path d="M0 1h2.5l2 5.5h6L12 2H3.5" fill="none" stroke="#555"/></svg></span><span><svg width="10" height="9"><rect x=".5" y="2.5" width="7" height="6" fill="none" stroke="#555"/><path d="M2.5 .5h7v6" fill="none" stroke="#555"/></svg></span><span><svg width="10" height="10"><circle cx="4" cy="4" r="3.2" fill="none" stroke="#555"/><path d="M6.5 6.5 9.5 9.5" stroke="#555"/></svg></span></div></div>
  <div class="abs card" style="left:419px;top:549px"><div class="img" role="img" aria-label="Round multicoloured jute rug on a dark floor" style="background:linear-gradient(170deg,#eee,#c9b78f 45%,#3d2f2a 75%)"></div><div class="name">Lorem ipsum</div><div class="price">$100.95</div><div class="actions"><span><svg width="12" height="10"><path d="M0 1h2.5l2 5.5h6L12 2H3.5" fill="none" stroke="#555"/></svg></span><span><svg width="10" height="9"><rect x=".5" y="2.5" width="7" height="6" fill="none" stroke="#555"/><path d="M2.5 .5h7v6" fill="none" stroke="#555"/></svg></span><span><svg width="10" height="10"><circle cx="4" cy="4" r="3.2" fill="none" stroke="#555"/><path d="M6.5 6.5 9.5 9.5" stroke="#555"/></svg></span></div></div>
  <div class="abs card" style="left:584px;top:549px"><div class="img" role="img" aria-label="White decorative head with colourful felt ball garlands" style="background:linear-gradient(160deg,#f3f1ee,#ddd6cf 60%,#e4a3a9)"></div><div class="name">Lorem ipsum</div><div class="price">$100.95</div><div class="actions"><span><svg width="12" height="10"><path d="M0 1h2.5l2 5.5h6L12 2H3.5" fill="none" stroke="#555"/></svg></span><span><svg width="10" height="9"><rect x=".5" y="2.5" width="7" height="6" fill="none" stroke="#555"/><path d="M2.5 .5h7v6" fill="none" stroke="#555"/></svg></span><span><svg width="10" height="10"><circle cx="4" cy="4" r="3.2" fill="none" stroke="#555"/><path d="M6.5 6.5 9.5 9.5" stroke="#555"/></svg></span></div></div>

  <div class="abs card" style="left:90px;top:745px"><div class="img" role="img" aria-label="Place setting with cutlery and green napkin" style="background:linear-gradient(160deg,#6f5a3a,#e8e2d6 50%,#d6cbb9)"></div><div class="name">Lorem ipsum</div><div class="price">$199.00</div><div class="actions"><span><svg width="12" height="10"><path d="M0 1h2.5l2 5.5h6L12 2H3.5" fill="none" stroke="#555"/></svg></span><span><svg width="10" height="9"><rect x=".5" y="2.5" width="7" height="6" fill="none" stroke="#555"/><path d="M2.5 .5h7v6" fill="none" stroke="#555"/></svg></span><span><svg width="10" height="10"><circle cx="4" cy="4" r="3.2" fill="none" stroke="#555"/><path d="M6.5 6.5 9.5 9.5" stroke="#555"/></svg></span></div></div>
  <div class="abs card" style="left:255px;top:745px"><div class="img" role="img" aria-label="Pink towel with bath brush and beads" style="background:linear-gradient(160deg,#f6eef0,#e77fa6 55%,#d24f82)"></div><div class="name">Lorem ipsum</div><div class="price">$100.95</div><div class="actions"><span><svg width="12" height="10"><path d="M0 1h2.5l2 5.5h6L12 2H3.5" fill="none" stroke="#555"/></svg></span><span><svg width="10" height="9"><rect x=".5" y="2.5" width="7" height="6" fill="none" stroke="#555"/><path d="M2.5 .5h7v6" fill="none" stroke="#555"/></svg></span><span><svg width="10" height="10"><circle cx="4" cy="4" r="3.2" fill="none" stroke="#555"/><path d="M6.5 6.5 9.5 9.5" stroke="#555"/></svg></span></div></div>
  <div class="abs card" style="left:419px;top:745px"><div class="img" role="img" aria-label="Dark vases and patterned cushion on a mint wall" style="background:linear-gradient(160deg,#8fd3c0,#5b4a42 55%,#2f2a28)"></div><div class="name">Lorem ipsum</div><div class="price">$100.95</div><div class="actions"><span><svg width="12" height="10"><path d="M0 1h2.5l2 5.5h6L12 2H3.5" fill="none" stroke="#555"/></svg></span><span><svg width="10" height="9"><rect x=".5" y="2.5" width="7" height="6" fill="none" stroke="#555"/><path d="M2.5 .5h7v6" fill="none" stroke="#555"/></svg></span><span><svg width="10" height="10"><circle cx="4" cy="4" r="3.2" fill="none" stroke="#555"/><path d="M6.5 6.5 9.5 9.5" stroke="#555"/></svg></span></div></div>
  <div class="abs card" style="left:584px;top:745px"><div class="img" role="img" aria-label="Living room with a bright patchwork rug" style="background:linear-gradient(170deg,#f2f2f2,#7fb6d4 45%,#d8467a 75%,#f0b52a)"></div><div class="name">Lorem ipsum</div><div class="price">$100.95</div><div class="actions"><span><svg width="12" height="10"><path d="M0 1h2.5l2 5.5h6L12 2H3.5" fill="none" stroke="#555"/></svg></span><span><svg width="10" height="9"><rect x=".5" y="2.5" width="7" height="6" fill="none" stroke="#555"/><path d="M2.5 .5h7v6" fill="none" stroke="#555"/></svg></span><span><svg width="10" height="10"><circle cx="4" cy="4" r="3.2" fill="none" stroke="#555"/><path d="M6.5 6.5 9.5 9.5" stroke="#555"/></svg></span></div></div>
</section>

<div class="abs divider"></div>
<div class="abs partners">
  <span><i></i>Ferrow</span><span>Lintelco</span><span>kestrel</span><span><i></i>Palewick</span><span>Ostrand</span><span><i></i>Meridel</span><span>Halvorsen</span><span>Brindlewood</span>
</div>

<footer>
  <div class="abs footer"></div>
  <div class="abs fcol" style="left:98px;width:76px"><h3>Category</h3><ul><li>Rugs</li><li>Bathe</li><li>Dine</li><li>Decorative</li><li>Sleep</li></ul></div>
  <div class="abs fcol" style="left:214px;width:96px"><h3>Information</h3><ul><li>Home</li><li>About Us</li><li>Blog</li><li>Testimonials</li><li>Contact us</li></ul></div>
  <div class="abs fcol" style="left:343px;width:90px"><h3>Your Account</h3><ul><li>Order Status</li><li>My Wishlist</li><li>Order History</li><li>Newsletter</li></ul></div>
  <div class="abs fcol news" style="left:472px;width:145px"><h3>Newsletter Sign Up</h3><p>Lorem ipsudolor sit ec adipiscing elitsite amet</p><div class="field">Email Address</div><div class="btn">SUBSCRIBE</div></div>
  <div class="abs fcol social" style="left:648px;width:87px"><h3>Follow us</h3><ul><li><i></i>Chatterly</li><li><i></i>Peeplet</li><li><i></i>Orbitly</li><li><i></i>Workloop</li></ul></div>
  <div class="abs bottom"></div>
  <div class="abs copy">© 2014 studio nine harbors. All Right reserved</div>
  <div class="abs cards"><i></i><i></i><i></i><i></i><i></i></div>
</footer>

</body>
</html>
```